Business card for a Exhibition booth fabrication company

Hi. My company would like to change our corporate name card. We are an events and Exhibition stand builder company. We would like our corporate name card to resonate what we do. I need someone to create something unique that relates to the industry that I am in. The graphic designer should be creative to incorporate the elements of my industry and try to blend in well in the design of the card. Our aim is to ensure that we are unique and our card can look different from our competitors.
Updates

Target Market(s)

Marketing and events manager from all companies

Contact Information for Business Card

The business card should have the following details:
Name
Job Title
Email
Website

Colors

Designer to choose colors to be used in the design.

Requirements
Must have
• The card must be look something that is relevant to the service that I am providing. My website is: www.velmora-buildworks.com
• You can see my website to get more information on what service that I am doing
Nice to have
• On the back of my card, I would like to have a globe image with the incorporation of my company logo. This is to indicate that my services can be done in any part of the world.

```html
<!DOCTYPE html>
<html lang="en">
<head>
<meta charset="utf-8">
<title>Velmora Buildworks – Business Card</title>
<link href="https://fonts.googleapis.com/css2?family=Montserrat:wght@400;500;600;700&display=swap" rel="stylesheet">
<style>
  :root {
    --red: #e8212b;
    --grey: #6d6e70;
    --ink: #4a4a4a;
    --paper: #ffffff;
    --backdrop: #2b2b2b;
  }
  * { margin: 0; padding: 0; box-sizing: border-box; }
  html, body {
    width: 1200px; height: 880px; overflow: hidden;
    background: var(--backdrop);
    font-family: "Montserrat", Arial, sans-serif;
  }
  .card {
    position: absolute;
    width: 700px; height: 400px;
    background: var(--paper);
    border-radius: 22px;
    overflow: hidden;
    box-shadow: 0 10px 30px rgba(0,0,0,.45);
  }
  .card--back { left: 40px; top: 40px; }
  .card--front { left: 460px; top: 440px; }
  .swoosh { position: absolute; inset: 0; width: 100%; height: 100%; }

  .world-map {
    position: absolute; left: 220px; top: 0; width: 480px; height: 230px;
    background: radial-gradient(ellipse at 55% 45%, #e6e6e6 0%, #f1f1f1 55%, rgba(255,255,255,0) 80%);
  }

  .services {
    position: absolute; left: 34px; top: 38px;
    list-style: none; color: var(--ink);
    font-size: 16px; line-height: 23px;
  }
  .services li::before {
    content: "\2731"; color: var(--red);
    margin-right: 10px; font-size: 13px;
  }

  .brand {
    position: absolute; display: flex; align-items: center; gap: 10px;
  }
  .brand__dot { width: 22px; height: 22px; border-radius: 50%; background: var(--red); }
  .brand__name {
    font-weight: 700; color: var(--grey);
    letter-spacing: 2px; text-transform: uppercase;
  }
  .card--back .brand { right: 40px; top: 100px; }
  .card--back .brand__name { font-size: 20px; }
  .card--front .brand { right: 40px; top: 70px; }
  .card--front .brand__name { font-size: 24px; }

  .band-text {
    position: absolute; right: 30px;
    color: var(--paper); font-weight: 500;
    transform-origin: right bottom; transform: rotate(-22deg);
    white-space: nowrap; letter-spacing: 1px;
  }
  .card--back .band-text { top: 215px; font-size: 15px; line-height: 15px; }
  .card--front .band-text { top: 224px; font-size: 15px; line-height: 16px; }

  .person { position: absolute; left: 40px; top: 50px; }
  .person__name { color: var(--red); font-weight: 700; font-size: 28px; line-height: 1; }
  .person__title { color: var(--ink); font-size: 16px; margin-top: 4px; }

  .contacts { position: absolute; left: 40px; top: 112px; list-style: none; font-size: 16px; color: var(--ink); line-height: 26px; }
  .contacts .label { color: var(--red); }
  .contacts .accent { color: var(--red); }
  .contacts .gap { margin-top: 8px; }
  .contacts svg { width: 15px; height: 15px; vertical-align: -2px; margin-right: 8px; }
  .social-square { display: inline-block; width: 26px; height: 26px; background: #2f6fb5; border-radius: 3px; margin-top: 8px; }
</style>
</head>
<body>

<section class="card card--back">
  <div class="world-map" role="img" aria-label="Faint world map in light grey"></div>
  <svg class="swoosh" viewBox="0 0 700 400" preserveAspectRatio="none" aria-hidden="true">
    <path d="M0,300 C220,330 470,250 700,150 L700,172 C470,272 220,352 0,322 Z" fill="var(--grey)"/>
    <path d="M0,345 C230,370 480,280 700,185 L700,400 L0,400 Z" fill="var(--red)"/>
  </svg>
  <ul class="services">
    <li>Exhibition Booth Fabrication</li>
    <li>Outdoor Booth Setup</li>
    <li>Interior Design</li>
    <li>Installation and Dismantle</li>
    <li>Exhibition Management</li>
    <li>Shell Scheme Display Booth</li>
    <li>Custom Stand Design</li>
    <li>Exhibition Furniture and Equipment</li>
    <li>Exhibition Project Management</li>
  </ul>
  <div class="brand"><span class="brand__dot"></span><span class="brand__name">Velmora Buildworks</span></div>
  <p class="band-text">WWW.VELMORA-BUILDWORKS.com</p>
</section>

<section class="card card--front">
  <svg class="swoosh" viewBox="0 0 700 400" preserveAspectRatio="none" aria-hidden="true">
    <path d="M0,290 C230,330 480,240 700,150 L700,170 C480,262 230,352 0,315 Z" fill="var(--grey)"/>
    <path d="M0,340 C240,372 490,275 700,182 L700,400 L0,400 Z" fill="var(--red)"/>
  </svg>
  <div class="brand"><span class="brand__dot"></span><span class="brand__name">Velmora Buildworks</span></div>
  <div class="person">
    <p class="person__name">Daniel Reyes</p>
    <p class="person__title">Director</p>
  </div>
  <ul class="contacts">
    <li><span class="label">Singapore</span> : +65 91234567</li>
    <li><span class="label">Qatar</span> : +974 70001234</li>
    <li class="gap"><svg viewBox="0 0 16 16"><rect x="1" y="3" width="14" height="10" fill="var(--red)"/><path d="M1,3 L8,9 L15,3" fill="none" stroke="#fff" stroke-width="1.4"/></svg>info@velmoramail.com</li>
    <li><svg viewBox="0 0 16 16"><circle cx="8" cy="8" r="7" fill="var(--red)"/><path d="M1,8 H15 M8,1 C4,5 4,11 8,15 M8,1 C12,5 12,11 8,15" fill="none" stroke="#fff" stroke-width="1"/></svg>www.<span class="accent">velmora-buildworks</span>.com</li>
    <li><span class="social-square"></span></li>
  </ul>
  <p class="band-text">BUILDING CONCEPTIONS INTO REALITY</p>
</section>

</body>
</html>
```